Road Construction Company needs business cards

We would like a new business card designed for our business.

We're a road construction company based in Qld, Australia.

Can the business card please have the following information on it.

Name: Warren Halbeck
Position: General Manager
Phone: 0472 915 348
Email: Warren.halbeck@tovrin.com.au
Address: 87 Marrow Ave, Pendlebay, QLD, 4023
Website: www.tovrin.com.au

Visually we'd like the card to be professional and simple.

Attached is our logo.

Our website is www.tovrin.com.au

Target Market(s)

Men aged 25-60

Contact Information for Business Card

As listed in project description

Font styles to use
Serif

Requirements
Must have
• Large logo on back of card

```html
<!DOCTYPE html>
<html lang="en">
<head>
<meta charset="utf-8">
<title>Tovrin – Business Card</title>
<link href="https://fonts.googleapis.com/css2?family=Poppins:wght@400;500;700;800&display=swap" rel="stylesheet">
<style>
  :root {
    --stage: #2a2a2c;
    --paper: #ffffff;
    --brand-blue: #1b5cc0;
    --brand-navy: #1a4fae;
    --accent-sky: #2b9fe0;
    --ink: #3a3a3a;
    --pattern-light: #2a6fd0;
  }
  * { box-sizing: border-box; margin: 0; padding: 0; }
  html, body {
    width: 1200px; height: 904px; overflow: hidden;
    background: var(--stage);
    font-family: "Poppins", sans-serif;
  }
  .stage { position: relative; width: 1200px; height: 904px; }
  .card {
    position: absolute; left: 320px; width: 560px; height: 320px;
    overflow: hidden; border-radius: 2px;
    box-shadow: 0 10px 26px rgba(0,0,0,.45);
  }
  .card--front { top: 104px; background: var(--paper); }
  .card--back { top: 480px; background: linear-gradient(135deg, #1d63c8 0%, #1753b5 60%, #1449a6 100%); }

  .front-shapes { position: absolute; inset: 0; width: 100%; height: 100%; }
  .front-shapes polygon { fill: var(--brand-blue); }

  .front-content { position: absolute; left: 40px; top: 40px; }
  .wordmark {
    font-weight: 800; font-size: 40px; letter-spacing: 1px;
    color: var(--brand-navy); line-height: 1;
  }
  .person { margin-top: 34px; }
  .person__name { font-weight: 700; font-size: 22px; color: var(--brand-navy); line-height: 1.1; }
  .person__role { font-weight: 400; font-size: 16px; color: var(--accent-sky); margin-top: 2px; }
  .divider { width: 26px; height: 2px; background: var(--accent-sky); margin: 12px 0 12px; }
  .address { font-size: 12px; color: var(--ink); line-height: 1.45; }
  .contacts { list-style: none; margin-top: 4px; }
  .contacts li {
    display: flex; align-items: center; gap: 8px;
    font-size: 12px; color: var(--ink); line-height: 1.55;
  }
  .contacts svg { width: 11px; height: 11px; fill: var(--brand-navy); flex: none; }

  .back-pattern { position: absolute; inset: 0;
    background: linear-gradient(120deg, rgba(255,255,255,.10) 0%, rgba(255,255,255,.04) 55%, rgba(255,255,255,0) 100%); }
  .back-logo {
    position: absolute; inset: 0; display: flex; align-items: center; justify-content: center;
  }
  .back-logo .wordmark { color: #ffffff; font-size: 64px; letter-spacing: 2px; }
</style>
</head>
<body>
<main class="stage">
  <section class="card card--front" aria-label="Business card front">
    <svg class="front-shapes" viewBox="0 0 100 100" preserveAspectRatio="none" aria-hidden="true">
      <polygon points="62,0 100,0 100,74"/>
      <polygon points="52,100 73,47 100,74 100,100"/>
    </svg>
    <div class="front-content">
      <div class="wordmark">TOVRIN</div>
      <div class="person">
        <div class="person__name">Warren Halbeck</div>
        <div class="person__role">General Manager</div>
      </div>
      <div class="divider"></div>
      <p class="address">87 Marrow Ave,<br>Pendlebay, QLD, 4023</p>
      <ul class="contacts">
        <li>
          <svg viewBox="0 0 24 24" aria-hidden="true"><path d="M6.6 10.8a15.1 15.1 0 0 0 6.6 6.6l2.2-2.2c.3-.3.7-.4 1-.2 1.1.4 2.3.6 3.6.6.6 0 1 .4 1 1V20c0 .6-.4 1-1 1A17 17 0 0 1 3 4c0-.6.4-1 1-1h3.5c.6 0 1 .4 1 1 0 1.3.2 2.5.6 3.6.1.3 0 .7-.2 1z"/></svg>
          0472 915 348
        </li>
        <li>
          <svg viewBox="0 0 24 24" aria-hidden="true"><path d="M2 5h20v14H2z M2 5l10 8 10-8" fill="none" stroke="#1a4fae" stroke-width="2.4"/></svg>
          Warren.halbeck@tovrin.com.au
        </li>
        <li>
          <svg viewBox="0 0 24 24" aria-hidden="true"><circle cx="12" cy="12" r="9.5" fill="none" stroke="#1a4fae" stroke-width="2.2"/><path d="M2.5 12h19M12 2.5c3 3 3 16 0 19M12 2.5c-3 3-3 16 0 19" fill="none" stroke="#1a4fae" stroke-width="1.8"/></svg>
          www.tovrin.com.au
        </li>
      </ul>
    </div>
  </section>

  <section class="card card--back" aria-label="Business card back">
    <div class="back-pattern" role="img" aria-label="Faint repeating decorative pattern in lighter blue"></div>
    <div class="back-logo">
      <div class="wordmark">TOVRIN</div>
    </div>
  </section>
</main>
</body>
</html>
```